I have a business that exists already (Linden Conservatory of Music) that we offer music lessons to all instruments. I recently opened a smaller version called CHORDS by Linden that will only teach piano lessons. What I'm looking for now is a 3 page Website on word press. After I choose the design I like I want to be able to take over the website and bring it to our hosting company. We want full control of it and our team will take over. The reason I'm doing this is to have other visions and ideas from others. The first page will be about the company and our message/vision. Second page about the piano lessons. The third will be about franchising this concept "Chords by Linden" Attached are 3 Logos . Please refer to our existing website www.lindenmusicconservatory.example to look at our piano page and franchising page. Please feel free to message me if you need more info. Thanks
Please note I do not want the new website (Chords by Linden) To look like the other Website (Linden Conservatory of Music) Fresh new look. I do not want the colours red or using the Red logo. I only provided it so that you have an Idea of What the other business looks like and that you can take the piano content and franchise content off of it. Chords by Linden is smaller concept and only piano lessons.
Thanks
Only Piano lessons for all students
3 page

```html
<!DOCTYPE html>
<html lang="en">
<head>
<meta charset="utf-8">
<title>Chords by Linden – Piano Lessons</title>
<link rel="stylesheet" href="https://fonts.googleapis.com/css2?family=Cinzel:wght@400;500&family=PT+Serif:ital,wght@0,400;0,700;1,400&family=Great+Vibes&display=swap">
<style>
:root{
  --ink:#111111;
  --black:#000000;
  --white:#ffffff;
  --gold:#f5b400;
  --mist:#f2f2f2;
  --rule:#c9c9c9;
  --text:#333333;
  --muted:#5a5a5a;
}
*{box-sizing:border-box;margin:0;padding:0}
html,body{width:1200px;height:3217px;overflow:hidden}
body{position:relative;background:var(--white);font-family:"PT Serif",Georgia,serif;color:var(--text)}
.abs{position:absolute}
.script{font-family:"Great Vibes",cursive}
.heading{font-family:"Cinzel",serif;font-weight:400;color:var(--ink)}
.chevrons{font-family:"PT Serif",serif;color:var(--gold);font-size:.7em;margin-left:8px}
.gold-rule{display:block;width:34px;height:2px;background:var(--gold)}

/* Hero */
.hero{position:absolute;left:0;top:0;width:1200px;height:740px}
.brand{position:absolute;left:144px;top:22px;display:flex;align-items:center;gap:10px;color:var(--white);font-family:"Cinzel",serif;font-size:30px;line-height:1}
.brand-dot{width:12px;height:12px;border-radius:50%;background:var(--white)}
.main-nav{position:absolute;top:40px;left:596px;display:flex;gap:36px;font-family:"Cinzel",serif;font-size:13.5px;letter-spacing:1px;color:var(--white)}
.main-nav .current{color:var(--gold)}
.hero-copy{position:absolute;left:143px;top:238px;color:var(--white)}
.hero-copy .lead{font-family:"Cinzel",serif;font-size:31px;text-transform:none;font-variant:normal;line-height:1.2;font-family:"PT Serif",serif}
.hero-copy .big{font-family:"Cinzel",serif;font-size:40px;letter-spacing:1px;margin:6px 0 4px}
.hero-copy .cta{margin-top:22px;font-size:30px;color:var(--gold)}

/* About */
.about{position:absolute;left:0;top:680px;width:1200px;text-align:center}
.about h2{font-size:30px;letter-spacing:1px}
.about h2 small{font-family:"Great Vibes",cursive;font-size:20px;text-transform:none;margin-left:4px}
.about .gold-rule{margin:8px auto 14px}
.about h3{font-style:italic;font-weight:400;font-size:22px;color:var(--ink);margin-bottom:12px}
.about p{width:880px;margin:0 auto 8px;font-size:14px;line-height:25px}
.about .more{font-size:25px;color:var(--muted);margin-top:22px}

/* Vision */
.vision{position:absolute;left:0;top:1038px;width:1200px;height:542px;background:var(--mist)}
.vision svg{position:absolute;left:0;top:0}
.vision-copy{position:absolute;left:635px;top:125px;width:420px}
.split-title{font-size:29px;letter-spacing:.5px;margin-bottom:14px}
.split-copy p{font-size:14px;line-height:25.5px;margin-bottom:6px}
.split-copy .cta{font-size:24px;color:var(--muted);margin-top:20px;margin-left:4px}

/* Programs */
.programs{position:absolute;left:0;top:1658px;width:1200px;height:543px}
.programs svg{position:absolute;left:0;top:0}
.programs-copy{position:absolute;left:142px;top:60px;width:440px}
.programs-copy h2{font-family:"PT Serif",serif;font-weight:400;font-size:24px;line-height:37px;color:var(--ink);margin-bottom:16px}
.benefits{list-style:none;margin-top:22px}
.benefits li{position:relative;padding-left:26px;font-size:14px;line-height:25.5px;margin-bottom:7px}
.benefits li svg{position:absolute;left:0;top:6px}
.programs-copy .cta{font-size:24px;color:var(--muted);margin-top:22px}

/* Quote */
.quote{position:absolute;left:0;top:2275px;width:1200px;height:210px;background:var(--mist);text-align:center}
.quote .mark{position:absolute;font-family:"PT Serif",serif;font-size:70px;color:#9a9a9a;line-height:1}
.quote blockquote{position:absolute;left:0;width:1200px;top:68px;font-style:italic;font-size:16px;color:var(--text)}
.quote .divider{position:absolute;left:508px;top:128px;width:184px;height:1px;background:var(--rule)}
.quote .divider::after{content:"";position:absolute;left:86px;top:0;border:6px solid transparent;border-top-color:var(--rule)}
.quote cite{position:absolute;left:0;width:1200px;top:152px;font-style:normal;font-weight:700;font-size:15px;color:var(--ink);letter-spacing:.5px}

/* Franchise */
.franchise{position:absolute;left:0;top:2560px;width:1200px;text-align:center}
.franchise h2{font-size:40px;letter-spacing:1.5px}
.franchise p{font-size:17px;margin-top:10px;color:var(--ink)}
.franchise .more{font-size:32px;color:var(--muted);margin-top:18px}

/* Footer */
.site-footer{position:absolute;left:0;top:2640px;width:1200px;height:527px}
.site-footer svg.wave{position:absolute;left:0;top:0}
.footer-brand{position:absolute;left:792px;top:200px;display:flex;align-items:center;gap:10px;color:var(--white);font-family:"Cinzel",serif;font-size:40px}
.contact-cards{position:absolute;left:0;top:0;width:1200px}
.contact-card{position:absolute;top:330px;width:260px;margin-left:-130px;text-align:center;color:var(--white);font-size:13.5px;line-height:21px}
.contact-card .badge{width:70px;height:70px;border-radius:50%;background:var(--white);margin:0 auto 16px;display:flex;align-items:center;justify-content:center}
.contact-card .label{font-family:"Cinzel",serif;font-size:14px;letter-spacing:.5px}
.copyright{position:absolute;left:0;top:3167px;width:1200px;height:50px;background:var(--gold);color:var(--ink);font-size:14px}
.copyright p{position:absolute;left:142px;top:16px}
.social{position:absolute;left:950px;top:18px;display:flex;gap:14px}
.social span{width:12px;height:12px;border-radius:50%;background:var(--ink)}
</style>
</head>
<body>

<header class="hero">
  <svg width="1200" height="740" viewBox="0 0 1200 740">
    <defs>
      <linearGradient id="pianoTone" x1="0" y1="0" x2="1" y2="1">
        <stop offset="0" stop-color="#000"/>
        <stop offset=".35" stop-color="#d8d8d8"/>
        <stop offset=".6" stop-color="#8a8a8a"/>
        <stop offset="1" stop-color="#1a1a1a"/>
      </linearGradient>
      <clipPath id="heroShape">
        <path d="M0 0H1200V700C1130 600 1000 540 820 540C640 540 560 600 400 610C230 620 60 580 0 470Z"/>
      </clipPath>
    </defs>
    <path d="M0 0H1200V700C1130 600 1000 540 820 540C640 540 560 600 400 610C230 620 60 580 0 470Z" fill="var(--black)"/>
    <g clip-path="url(#heroShape)">
      <rect x="450" y="80" width="750" height="640" fill="url(#pianoTone)" role="img" aria-label="Photo of a grand piano keyboard in dramatic light"/>
    </g>
    <path d="M0 482C60 592 230 632 400 622C560 612 640 552 820 552C1000 552 1130 612 1200 712" fill="none" stroke="#a9a9a9" stroke-width="9"/>
  </svg>
  <div class="brand"><span class="brand-dot"></span>CHORDS by Linden</div>
  <nav class="main-nav">
    <span class="current">HOME</span><span>PIANO LESSONS</span><span>FRANCHISING</span><span>CONTACT US</span>
  </nav>
  <div class="hero-copy">
    <div class="lead">We Will Provide</div>
    <div class="big">Piano Lessons</div>
    <div class="lead">For All Students</div>
    <div class="cta script">Contact Us Today<span class="chevrons">&gt;&gt;</span></div>
  </div>
</header>

<section class="about">
  <h2 class="heading">About Chords <small>by Linden</small></h2>
  <span class="gold-rule"></span>
  <h3>Playing the Piano</h3>
  <p>When you think of a piano, you probably envision black and white keys but the piano is more than those harmonious sounds created by the player. The versatility and the musicianship instilled into the player from those keys is the true magic that comes from playing piano!</p>
  <p>Starting from the grassroots, experience different methods and styles of playing piano. To mark the milestones of progression, engage in one of Linden’s many unique performance opportunities like annual festival competitions, recitals or our examinations (Linden &amp; NMB). Penultimately, at the end of the journey, join our elite teaching program to bring the same joy of learning the piano to another student.</p>
  <div class="more script">Read More<span class="chevrons">&gt;&gt;</span></div>
</section>

<section class="vision">
  <svg width="600" height="542" viewBox="0 0 600 542">
    <polygon points="0,0 537,0 578,542 0,542" fill="#cdb79e" role="img" aria-label="Photo of a teacher and a young student playing a white piano together"/>
    <polygon points="537,0 555,0 596,542 578,542" fill="var(--gold)"/>
  </svg>
  <div class="vision-copy split-copy">
    <h2 class="heading split-title">OUR VISION</h2>
    <span class="gold-rule" style="margin-bottom:18px"></span>
    <p>Our Mission is Lorem ipsum dolor sit amet, consectetuer adipiscig elit, sed diama nonummy nibh euismod tincidunt ut laoreet dolore magna aliquam erat volutpat. Ut wisi enim ad minim veniam.</p>
    <p>Lorem hendrerit in vulputate velit esse molestie consequat, velocity illum dolore eu feugiat nulla facilisis at vero eros et accumsan etlict iusto odio dignissim qui blandit praesent luptatum zzril delenit loei augue duis dolore te feugait nulla facilisi.</p>
    <div class="cta script">Contact Us Today<span class="chevrons">&gt;&gt;</span></div>
  </div>
</section>

<section class="programs">
  <svg width="1200" height="543" viewBox="0 0 1200 543">
    <polygon points="604,0 619,0 662,543 647,543" fill="var(--gold)"/>
    <polygon points="619,0 1200,0 1200,543 662,543" fill="#8a6a52" role="img" aria-label="Photo of children playing keyboard and strings in a group class"/>
  </svg>
  <div class="programs-copy">
    <h2>OUR PROGRAMS ALSO PROVIDE STUDENTS THE OPPORTUNITY TO:</h2>
    <span class="gold-rule"></span>
    <ul class="benefits">
      <li><svg width="14" height="12" viewBox="0 0 14 12"><path d="M1 6H12M8 2L12 6L8 10" fill="none" stroke="var(--gold)" stroke-width="1.6"/></svg>Participate in large-scale performances.</li>
      <li><svg width="14" height="12" viewBox="0 0 14 12"><path d="M1 6H12M8 2L12 6L8 10" fill="none" stroke="var(--gold)" stroke-width="1.6"/></svg>Perform at Linden’s many community events on a regular basis.</li>
      <li><svg width="14" height="12" viewBox="0 0 14 12"><path d="M1 6H12M8 2L12 6L8 10" fill="none" stroke="var(--gold)" stroke-width="1.6"/></svg>Access the GTA’s coolest Broadcast stage</li>
      <li><svg width="14" height="12" viewBox="0 0 14 12"><path d="M1 6H12M8 2L12 6L8 10" fill="none" stroke="var(--gold)" stroke-width="1.6"/></svg>Attend Clinics, Masterclasses, and Jam Nights</li>
      <li><svg width="14" height="12" viewBox="0 0 14 12"><path d="M1 6H12M8 2L12 6L8 10" fill="none" stroke="var(--gold)" stroke-width="1.6"/></svg>Access the Linden Rocks band program. Linden’s Band Program empowers and electrifies students to come together, create music and confidently hit the stage with their own band identity while having fun and honing their instrument.</li>
      <li><svg width="14" height="12" viewBox="0 0 14 12"><path d="M1 6H12M8 2L12 6L8 10" fill="none" stroke="var(--gold)" stroke-width="1.6"/></svg>Register in our elite teaching program to learn how to pass on the magic and passion of playing the piano to students.</li>
    </ul>
    <div class="cta script">Contact Us Today<span class="chevrons">&gt;&gt;</span></div>
  </div>
</section>

<section class="quote">
  <span class="mark" style="left:272px;top:30px">&ldquo;</span>
  <blockquote>“Life is like a piano. What you get out of it depends on how you play it.”</blockquote>
  <span class="mark" style="left:886px;top:72px">&rdquo;</span>
  <span class="divider"></span>
  <cite>- MARION HALE</cite>
</section>

<section class="franchise">
  <h2 class="heading">Franchise Opportunities</h2>
  <p>BE PART OF THE LINDEN CONSERVATORY FAMILY</p>
</section>

<footer class="site-footer">
  <svg class="wave" width="1200" height="527" viewBox="0 0 1200 527">
    <path d="M0 0C150 150 350 210 620 190C860 172 1100 170 1200 300V527H0Z" fill="var(--black)"/>
    <path d="M0 -8C150 142 350 202 620 182C860 164 1100 162 1200 292" fill="none" stroke="#a9a9a9" stroke-width="9"/>
  </svg>
  <div class="abs script" style="left:0;top:48px;width:1200px;text-align:center;font-size:32px;color:var(--muted)">Know More<span class="chevrons">&gt;&gt;</span></div>
  <div class="footer-brand"><span class="brand-dot"></span>CHORDS by Linden</div>
  <div class="contact-cards">
    <div class="contact-card" style="left:313px">
      <div class="badge"><svg width="22" height="30" viewBox="0 0 22 30"><path d="M11 1C5.5 1 1 5.3 1 10.8C1 18 11 29 11 29S21 18 21 10.8C21 5.3 16.5 1 11 1Z" fill="var(--gold)"/><circle cx="11" cy="11" r="4" fill="var(--white)"/></svg></div>
      <div class="label">CHORDS BY LINDEN</div>
      <div>123, Building Name, Street</div>
      <div>City, State XY 123456</div>
    </div>
    <div class="contact-card" style="left:607px">
      <div class="badge"><svg width="28" height="28" viewBox="0 0 28 28"><path d="M7 3L11 9L8.5 11.5C10 15 13 18 16.5 19.5L19 17L25 21L22.5 25C13 25 3 15 3 5.5Z" fill="var(--gold)"/></svg></div>
      <div class="label">CALL US</div>
      <div>1-800-555-0142</div>
    </div>
    <div class="contact-card" style="left:889px">
      <div class="badge"><svg width="30" height="22" viewBox="0 0 30 22"><rect x="1" y="1" width="28" height="20" fill="var(--gold)"/><path d="M1 1L15 12L29 1" fill="none" stroke="var(--white)" stroke-width="2"/></svg></div>
      <div class="label">EMAIL US</div>
      <div>inquiry@chordsbylinden.example</div>
    </div>
  </div>
</footer>

<div class="copyright">
  <p>Copyright © 2020 <strong>Chords by Linden</strong>. All Rights Reserved.</p>
  <div class="social" aria-label="Social media links"><span></span><span></span><span></span><span></span></div>
</div>

</body>
</html>
```